Healthy Food Healthy Brain Rack Card

We want a new 2 page (front and page) 3.67" x 8.5" rack card. This rack card is the first of a series we are creating. We will have five more eventually.

The minimum font size for the text on the front is 11 point and also for other main body text.

Use the text on the word document.

The images and layout in the word document are just sample ideas we had.

We have a subscripton to plivora pics images so prefer to get images from there or free high quality images.

The document is for older readers. Do not put text over graphics and keep it simple and easy to read with high contrast.

We are open to any color scheme, though something that conveys fresh and healthy, is good.

We want some very simple design element(s) incorporated that convey Native American communities or heritage. But NO head dress, teepee graphics, etc.

At the top, of the first page we would like a collage of healthy food images. This can include fish, chicken, fresh vegetables, berries, brown rice, etc.

On the back side, the text below the brown box on the word document with the title "mock up" can be smaller as needed.

Please remember to include the funding statement - it can be in a very small font 6/7 point.

For more information about our project, please visit https://veltronaq.org/mind-care/

```html
<!DOCTYPE html>
<html lang="en">
<head>
<meta charset="utf-8">
<title>Healthy Food Healthy Brain – Rack Card</title>
<link rel="stylesheet" href="https://fonts.googleapis.com/css2?family=Open+Sans:ital,wght@0,400;0,600;0,700;1,600;1,700&family=Oswald:wght@600&display=swap">
<style>
  :root {
    --page-bg: #f3f3f3;
    --card-bg: #ffffff;
    --brand-red: #981b2d;
    --brand-teal: #5ba5b1;
    --ink: #222222;
    --white: #ffffff;
  }
  * { box-sizing: border-box; margin: 0; padding: 0; }
  html, body { width: 1200px; height: 1200px; overflow: hidden; }
  body {
    position: relative;
    background: var(--page-bg);
    font-family: "Open Sans", Arial, sans-serif;
    color: var(--ink);
  }
  .card {
    position: absolute;
    top: 75px;
    width: 461px;
    height: 1068px;
    background: var(--card-bg);
    overflow: hidden;
  }
  .card--front { left: 110px; }
  .card--back { left: 607px; }

  /* ---------- Front ---------- */
  .collage { position: absolute; top: 4px; left: 6px; width: 449px; height: 280px; }
  .collage__photo { position: absolute; }
  .photo-produce-left { left: 0; top: 0; width: 82px; height: 280px;
    background: linear-gradient(170deg, #8a7a52 0%, #4f7a3a 30%, #d9d2b8 50%, #3f7a2e 70%, #c7473a 100%); }
  .photo-proteins { left: 84px; top: 0; width: 280px; height: 84px;
    background: linear-gradient(90deg, #e4dcdc 0%, #b9a79a 35%, #d8d4d0 60%, #c9b1a4 100%); }
  .photo-citrus { left: 84px; top: 196px; width: 280px; height: 84px;
    background: linear-gradient(90deg, #6f9b3c 0%, #e8e4d6 30%, #e86a4f 50%, #efe7d8 75%, #e9e1cf 100%); }
  .photo-produce-right { left: 366px; top: 0; width: 83px; height: 280px;
    background: linear-gradient(180deg, #b9a57a 0%, #d9b54a 20%, #c8302a 45%, #8a6a4c 75%, #b58a60 100%); }
  .title-box {
    position: absolute; left: 84px; top: 84px; width: 280px; height: 112px;
    background: var(--white);
    display: flex; flex-direction: column; align-items: center; justify-content: center;
  }
  .title-box__line {
    font-family: "Oswald", Impact, sans-serif; font-weight: 600;
    color: var(--brand-red); font-size: 39px; line-height: 45px; letter-spacing: 0.3px;
  }
  .intro {
    position: absolute; top: 303px; left: 26px; right: 26px;
    text-align: center; color: var(--brand-red);
    font-style: italic; font-weight: 600; font-size: 17px; line-height: 22.7px;
  }
  .steps-heading {
    position: absolute; top: 443px; left: 30px;
    font-weight: 600; font-size: 17px;
  }
  .steps {
    position: absolute; top: 485px; left: 30px; right: 20px;
    list-style: none; font-size: 17px; line-height: 28px;
  }
  .steps li { position: relative; padding-left: 14px; }
  .steps li::before { content: "•"; position: absolute; left: 0; }
  .closing {
    position: absolute; top: 807px; left: 30px; right: 24px;
    font-weight: 600; font-size: 17.5px; line-height: 28px;
  }
  .doctor-note {
    position: absolute; top: 886px; left: 20px; right: 20px;
    text-align: center; font-weight: 600; font-size: 18.5px; line-height: 24.5px;
    text-transform: uppercase;
  }
  .quote-band {
    position: absolute; top: 952px; left: 5px; width: 450px; height: 109px;
    background: var(--brand-red); color: var(--white);
    display: flex; align-items: center; justify-content: center; text-align: center;
    font-style: italic; font-weight: 600; font-size: 19.5px; line-height: 28px;
  }

  /* ---------- Back ---------- */
  .header-band {
    position: absolute; top: 0; left: 0; width: 461px; height: 98px;
    background: var(--brand-red); color: var(--white);
    display: flex; align-items: center; justify-content: center;
    font-weight: 700; font-size: 43px;
  }
  .recipe-photo {
    position: absolute; top: 118px; left: 34px; width: 176px; height: 179px;
    background: radial-gradient(circle at 60% 50%, #e98a6c 0%, #d9a38c 20%, #c8ccc6 45%, #d8dbda 70%, #bfc2c4 100%);
  }
  .recipe-caption {
    position: absolute; top: 297px; left: 34px; width: 176px; height: 56px;
    background: var(--brand-red); color: var(--white);
    display: flex; align-items: center; justify-content: center; text-align: center;
    font-weight: 600; font-size: 16.5px; line-height: 21px;
  }
  .ingredients {
    position: absolute; top: 118px; left: 221px; font-size: 17px; line-height: 21.8px;
  }
  .ingredients__title { font-weight: 700; }
  .ingredients ul { list-style: none; }
  .method-band {
    position: absolute; top: 372px; left: 0; width: 461px; height: 213px;
    background: var(--brand-red); color: var(--white);
    padding: 14px 14px 0; text-align: center; font-size: 17px; line-height: 22.6px;
  }
  .message-band {
    position: absolute; top: 585px; left: 0; width: 461px; height: 172px;
    background: var(--brand-teal); color: var(--white);
    display: flex; align-items: center; justify-content: center; text-align: center;
    padding: 0 18px;
    font-style: italic; font-weight: 700; font-size: 22.5px; line-height: 28px;
  }
  .resources { position: absolute; top: 770px; left: 17px; right: 19px; height: 120px; }
  .resources__heading { font-weight: 600; font-size: 15.5px; line-height: 20px; }
  .resource-col { position: absolute; top: 0; font-size: 12px; line-height: 14.5px; }
  .resource-col--left { left: 0; }
  .resource-col--right { right: 0; text-align: right; }
  .resource-col .resources__heading { margin-bottom: 6px; }
  .resource-name { font-weight: 600; }
  .resource-col--left .resource-name + .resource-name { margin-top: 7px; }
  .resource-center { position: absolute; top: 863px; left: 0; width: 461px; text-align: center; font-size: 12px; line-height: 14.5px; }
  .brand-mark {
    position: absolute; top: 905px; left: 80px;
    display: flex; align-items: center; gap: 14px;
  }
  .brand-mark__dot { width: 62px; height: 62px; border-radius: 50%; background: var(--brand-teal); }
  .brand-mark__name {
    color: var(--brand-teal); font-weight: 700; font-size: 17px; line-height: 20px;
    text-transform: uppercase;
  }
  .funding-band {
    position: absolute; top: 988px; left: 0; width: 461px; height: 80px;
    background: var(--brand-teal); color: var(--white);
    padding: 10px 17px 0; font-size: 9.3px; line-height: 14px;
  }
</style>
</head>
<body>

<section class="card card--front" aria-label="Rack card front">
  <div class="collage">
    <div class="collage__photo photo-produce-left" role="img" aria-label="Photo of fresh vegetables and fruit in paper bags"></div>
    <div class="collage__photo photo-proteins" role="img" aria-label="Photo of fish, lean meats and yogurt on a grey surface"></div>
    <div class="collage__photo photo-citrus" role="img" aria-label="Photo of grapefruit, broccoli, apple and potatoes"></div>
    <div class="collage__photo photo-produce-right" role="img" aria-label="Photo of tomatoes, lemon, pineapple and ginger in a box"></div>
    <div class="title-box">
      <span class="title-box__line">HEALTHY FOOD</span>
      <span class="title-box__line">HEALTHY BRAIN</span>
    </div>
  </div>

  <p class="intro">Everyone slows down as they get older, both in body and mind. Eating healthier food can help your overall health, including brain health. It may also reduce your risk for memory loss and problems thinking.</p>

  <h2 class="steps-heading">Healthier steps to protect your brain:</h2>
  <ul class="steps">
    <li>Eat more vegetables, fruits, whole grains, and lower-fat milk</li>
    <li>Use less salt and added sugar</li>
    <li>Eat more fish, chicken, turkey, beans, and nuts</li>
    <li>Cut down on bad fats (“saturated” and trans), cholesterol, and red meat</li>
    <li>Buy fresh, not packaged food when you can</li>
    <li>Limit how much alcohol you drink</li>
    <li>Learn your daily calorie needs for your body size</li>
    <li>Take care of your mental and spiritual health to support your physical and brain health</li>
  </ul>

  <p class="closing">Small changes can make a big difference for better brain health.</p>
  <p class="doctor-note">Talk to your doctor about more steps to healthier food choices.</p>

  <blockquote class="quote-band">“Without the elk, salmon, huckleberries,<br>shellfish, and cedar trees we are nobody…”<br>Lena Marrow (Coastal Elder)</blockquote>
</section>

<section class="card card--back" aria-label="Rack card back">
  <h1 class="header-band">Make This at Home</h1>

  <div class="recipe-photo" role="img" aria-label="Photo of salmon fillet with asparagus, peppers and lemon in a foil packet"></div>
  <div class="recipe-caption">Grilled Salmon and<br>Veggie Foil Packets</div>

  <div class="ingredients">
    <p class="ingredients__title">Ingredients:</p>
    <ul>
      <li>Salmon</li>
      <li>Asparagus</li>
      <li>Red or Green Peppers</li>
      <li>(Or any seasonal vegetable)</li>
      <li>Onion</li>
      <li>Lemon – sliced</li>
      <li>Basil</li>
      <li>Olive Oil</li>
      <li>Salt and Pepper</li>
      <li>Garlic Powder</li>
    </ul>
  </div>

  <p class="method-band">Cut asparagus, peppers, and onion into bite-size pieces. Cut salmon into 4-6 oz pieces. Tear tin foil large enough to wrap around salmon &amp; veggies (2 layers). Add veggies and salmon to foil. Drizzle with olive oil, season with salt, pepper, basil, garlic &amp; top with a piece of sliced lemon. Wrap foil tightly around food. Grill at 400 degrees for about 20 minutes. Careful opening!</p>

  <p class="message-band">Food &amp; drink are a source of strength and connection to community. A return to traditional food pathways and eating local, seasonal fresh foods make healthier eating easier.</p>

  <div class="resources">
    <div class="resource-col resource-col--left">
      <h3 class="resources__heading">For More Information</h3>
      <p class="resource-name">About Healthier Eating</p>
      <p class="resource-name">PlateGuide</p>
      <p>https://www.plateguide.org</p>
    </div>
    <div class="resource-col resource-col--right">
      <h3 class="resources__heading">About Brain Health</h3>
      <p class="resource-name">Resource Center for Tribal<br>Brain Health</p>
      <p>https://www.TribalBrainWell.org</p>
    </div>
  </div>

  <div class="resource-center">
    <p class="resource-name">National Memory Health Program</p>
    <p>https://www.memoryhealth.org/aging</p>
  </div>

  <div class="brand-mark">
    <span class="brand-mark__dot"></span>
    <span class="brand-mark__name">Tribal Brain Well<br>Resource Center</span>
  </div>

  <p class="funding-band">This product is supported by the National Health Agency (NHA) of the Department of Health Services (DHS) as part of a financial assistance award totaling $348,711 with 100 percent funded by NHA/DHS. The contents are those of the author(s) and do not necessarily represent the official views of, nor an endorsement, by NHA/DHS, or the agency.</p>
</section>

</body>
</html>
```